Advertisement Design

I'm looking for a post card sized advertisement piece that I will be dropping off to commercial and residential customers.
On one side I want it promoting carpet cleaning services and on the other side dryer vent cleaning services.
I've uploaded two different layouts of my company logo for you to choice from.
One batch will be printed with my Michigan Number
One batch will be printed with my Tennessee number
Will share contact numbers with the winner so just use a make up number
742-318-9516

```html
<!DOCTYPE html>
<html lang="en">
<head>
<meta charset="utf-8">
<title>Tidewell Carpet Cleaning Postcard</title>
<link href="https://fonts.googleapis.com/css2?family=Montserrat:wght@400;500;600;700;800&family=Raleway:wght@300;400&display=swap" rel="stylesheet">
<style>
  :root {
    --brand-blue: #1a7fc9;
    --frame-blue: #37a8e2;
    --ink-gray: #4a4b4d;
    --contact-ink: #3a3b3d;
    --band-dark: #2a2b2e;
    --divider: #6a6b6e;
    --paper: #ffffff;
    --backdrop: #4d4d4d;
  }
  * { margin: 0; padding: 0; box-sizing: border-box; }
  html, body { width: 1200px; height: 900px; overflow: hidden; }
  body { background: var(--backdrop); font-family: "Montserrat", sans-serif; }

  .postcard {
    position: absolute; left: 0; top: 21px;
    width: 1200px; height: 858px;
    background: var(--paper);
    overflow: hidden;
  }

  .brand { position: absolute; left: 53px; top: 98px; display: flex; align-items: center; gap: 16px; }
  .brand-square { width: 56px; height: 56px; background: var(--brand-blue); border-radius: 6px; }
  .brand-name { font-weight: 600; font-size: 40px; color: var(--brand-blue); letter-spacing: 1.5px; }

  .headline {
    position: absolute; left: 48px; top: 226px;
    font-weight: 700; font-size: 58px; line-height: 70px;
    color: var(--brand-blue); letter-spacing: -0.5px; white-space: nowrap;
  }
  .tagline {
    position: absolute; left: 50px; top: 298px;
    font-family: "Raleway", sans-serif; font-weight: 300; font-size: 39px; line-height: 42px;
    color: var(--ink-gray); text-transform: uppercase; white-space: nowrap;
  }
  .tagline strong { font-family: "Montserrat", sans-serif; font-weight: 700; font-size: 37px; }

  .service-band {
    position: absolute; left: 0; top: 440px; width: 1049px; height: 274px;
    background: var(--band-dark); border-bottom-right-radius: 14px;
  }
  .band-title {
    position: absolute; left: 50px; top: 6px;
    font-weight: 700; font-size: 33px; line-height: 40px; color: var(--brand-blue);
  }
  .band-copy {
    position: absolute; left: 50px; top: 47px; width: 515px;
    font-family: "Raleway", sans-serif; font-size: 13.5px; line-height: 17px; color: #fff;
  }
  .band-copy strong {
    display: block; max-width: 390px;
    font-family: "Montserrat", sans-serif; font-weight: 600; font-size: 13px;
  }

  .service-list { position: absolute; left: 0; top: 117px; width: 1049px; height: 145px; }
  .service {
    position: absolute; top: 0; width: 150px; margin-left: -75px;
    text-align: center; color: #fff; font-weight: 700; font-size: 15.5px; line-height: 20px;
  }
  .service-icon { display: block; width: 42px; height: 42px; margin: 0 auto 14px; }
  .divider { position: absolute; top: 2px; height: 118px; border-left: 1px dotted var(--divider); }

  .photo-frame {
    position: absolute; left: 872px; top: 25px; width: 304px; height: 306px;
    background: var(--frame-blue); border-radius: 30px;
  }
  .photo {
    position: absolute; left: 640px; top: 46px; width: 516px; height: 516px;
    border-radius: 30px;
    background: linear-gradient(205deg, #1d6fc4 0%, #2f79bf 28%, #b9b5ae 52%, #c6c2bb 70%, #a9a49d 100%);
  }

  .region { position: absolute; top: 735px; }
  .region h3 { font-weight: 700; font-size: 20px; line-height: 24px; color: var(--brand-blue); margin-bottom: 5px; }
  .contact-line {
    display: flex; align-items: center; gap: 10px;
    font-weight: 600; font-size: 16px; color: var(--contact-ink); height: 27px;
  }
  .contact-line svg { width: 14px; height: 14px; fill: var(--brand-blue); flex: none; }
  .region-mi { left: 50px; }
  .region-tn { left: 387px; }

  .web-bar {
    position: absolute; left: 695px; top: 749px; width: 505px; height: 64px;
    background: var(--band-dark); border-radius: 6px 0 0 6px;
    display: flex; align-items: center; padding-left: 22px;
    font-weight: 800; font-size: 30px; letter-spacing: 1.5px; color: #fff;
  }
  .web-bar span { color: var(--brand-blue); }
</style>
</head>
<body>
<main class="postcard">

  <div class="brand">
    <div class="brand-square"></div>
    <div class="brand-name">TIDEWELL</div>
  </div>

  <h1 class="headline">CARPET CLEANING</h1>
  <p class="tagline">Providing services<br>for both <strong>Residential</strong> &amp;<br><strong>Commercial clients.</strong></p>

  <div class="photo-frame"></div>
  <div class="photo" role="img" aria-label="Photo of a blue carpet cleaning wand gliding over freshly cleaned beige carpet beside a wall outlet and a blue-lit wall"></div>

  <section class="service-band">
    <h2 class="band-title">CARPET CLEANING</h2>
    <p class="band-copy"><strong>At Tidewell, we have been providing carpet cleaning services for more than 40 years.</strong>
    Using state-of-the-art industrial equipment combined with our years of service, there is not much that we cannot clean.Carpet cleaning services include:</p>

    <div class="service-list">
      <div class="service" style="left:90px">
        <svg class="service-icon" viewBox="0 0 42 42"><rect width="42" height="42" rx="4" fill="#1a7fc9"/><rect x="12" y="10" width="18" height="24" fill="#fff"/><g fill="#1a7fc9"><rect x="15" y="14" width="3" height="3"/><rect x="20" y="14" width="3" height="3"/><rect x="25" y="14" width="3" height="3"/><rect x="15" y="20" width="3" height="3"/><rect x="20" y="20" width="3" height="3"/><rect x="25" y="20" width="3" height="3"/><rect x="19" y="27" width="4" height="7"/></g></svg>
        Commercial<br>Carpet<br>Cleaning
      </div>
      <div class="divider" style="left:158px"></div>
      <div class="service" style="left:228px">
        <svg class="service-icon" viewBox="0 0 42 42"><rect width="42" height="42" rx="4" fill="#1a7fc9"/><path d="M8 21 L21 9 L34 21 Z" fill="#fff"/><rect x="12" y="20" width="18" height="13" fill="#fff"/><rect x="19" y="25" width="4" height="8" fill="#1a7fc9"/></svg>
        Residential<br>Carpet<br>Cleaning
      </div>
      <div class="divider" style="left:296px"></div>
      <div class="service" style="left:351px">
        <svg class="service-icon" viewBox="0 0 42 42"><rect width="42" height="42" rx="4" fill="#1a7fc9"/><rect x="10" y="9" width="22" height="24" fill="none" stroke="#fff" stroke-width="2.5"/><rect x="15" y="14" width="12" height="14" fill="#fff"/></svg>
        Rug<br>Cleaning
      </div>
      <div class="divider" style="left:407px"></div>
      <div class="service" style="left:485px">
        <svg class="service-icon" viewBox="0 0 42 42"><rect width="42" height="42" rx="4" fill="#1a7fc9"/><path d="M8 24 H34 L30 31 H12 Z" fill="#fff"/><rect x="15" y="18" width="12" height="5" fill="#fff"/><rect x="20" y="10" width="2" height="8" fill="#fff"/></svg>
        Boat, RV,<br>Aircraft<br>Carpet Cleaning
      </div>
      <div class="divider" style="left:574px"></div>
      <div class="service" style="left:639px">
        <svg class="service-icon" viewBox="0 0 42 42"><rect width="42" height="42" rx="4" fill="#1a7fc9"/><g fill="none" stroke="#fff" stroke-width="3" stroke-linecap="round"><path d="M14 32 C10 26 18 22 14 10"/><path d="M21 32 C17 26 25 22 21 10"/><path d="M28 32 C24 26 32 22 28 10"/></g></svg>
        Tile &amp; Grout<br>cleaning
      </div>
      <div class="divider" style="left:711px"></div>
      <div class="service" style="left:794px">
        <svg class="service-icon" viewBox="0 0 42 42"><rect width="42" height="42" rx="4" fill="#1a7fc9"/><path d="M7 10 L17 15 V33 H7 Z M35 10 L25 15 V33 H35 Z" fill="#fff"/><rect x="17" y="15" width="8" height="18" fill="none" stroke="#fff" stroke-width="2"/></svg>
        Corridor Carpet<br>Cleaning
      </div>
      <div class="divider" style="left:874px"></div>
      <div class="service" style="left:958px">
        <svg class="service-icon" viewBox="0 0 42 42"><rect width="42" height="42" rx="4" fill="#1a7fc9"/><rect x="12" y="12" width="18" height="10" rx="3" fill="#fff"/><rect x="8" y="19" width="26" height="9" rx="3" fill="#fff"/><rect x="11" y="28" width="3" height="4" fill="#fff"/><rect x="28" y="28" width="3" height="4" fill="#fff"/></svg>
        Upholstery<br>Cleaning
      </div>
    </div>
  </section>

  <div class="region region-mi">
    <h3>WEST MICHIGAN</h3>
    <div class="contact-line"><svg viewBox="0 0 24 24"><path d="M6.6 10.8a15.2 15.2 0 0 0 6.6 6.6l2.2-2.2a1 1 0 0 1 1-.25 11.4 11.4 0 0 0 3.6.57 1 1 0 0 1 1 1V20a1 1 0 0 1-1 1A17 17 0 0 1 3 4a1 1 0 0 1 1-1h3.5a1 1 0 0 1 1 1c0 1.25.2 2.45.57 3.6a1 1 0 0 1-.25 1z"/></svg>(742) 318-9516</div>
    <div class="contact-line"><svg viewBox="0 0 24 24"><path d="M2 5h20v14H2z"/><path d="M2 5l10 8 10-8" fill="none" stroke="#fff" stroke-width="1.8"/></svg>BILLING@TIDEWELLCLEAN.COM</div>
  </div>

  <div class="region region-tn">
    <h3>MIDDLE TENNESSEE</h3>
    <div class="contact-line"><svg viewBox="0 0 24 24"><path d="M6.6 10.8a15.2 15.2 0 0 0 6.6 6.6l2.2-2.2a1 1 0 0 1 1-.25 11.4 11.4 0 0 0 3.6.57 1 1 0 0 1 1 1V20a1 1 0 0 1-1 1A17 17 0 0 1 3 4a1 1 0 0 1 1-1h3.5a1 1 0 0 1 1 1c0 1.25.2 2.45.57 3.6a1 1 0 0 1-.25 1z"/></svg>(615) 555-0142</div>
    <div class="contact-line"><svg viewBox="0 0 24 24"><path d="M2 5h20v14H2z"/><path d="M2 5l10 8 10-8" fill="none" stroke="#fff" stroke-width="1.8"/></svg>DANA@TIDEWELLCLEAN.COM</div>
  </div>

  <div class="web-bar">www.<span>TidewellClean</span>.com</div>

</main>
</body>
</html>
```